Brightway Haul & Upkeep Services, are a company that offers a 'one stop shop' pre-move clean up a

I have already selected a logo which I would like on the front of the business cards along with phone numbers, web address and email which are:
0487650392
www.brightwayhaul.com.au
brightwayhaulandupkeep@mailbox.example

On the back of the card I would like to list some of the types of service we offer (clean - move - repairs/maintenance) which are:
CLEAN - windows, gutters, solar panels, driveways/paths, carpets.
MOVE - Small/medium size house/office moves, large item pick-up & delivery, yard clean-up and removal.
General maintenance and repairs.

I would like the blue logo on a gray background.

Thanks

```html
<!DOCTYPE html>
<html lang="en">
<head>
<meta charset="utf-8">
<title>Brightway Haul &amp; Upkeep Services – Business Card</title>
<link rel="stylesheet" href="https://fonts.googleapis.com/css2?family=Source+Sans+3:wght@400;600;700&display=swap">
<style>
  :root {
    --brand-blue: #1f6cb6;
    --ink: #1b1b1b;
    --card-white: #ffffff;
    --backdrop: #e7e5e2;
    --card-edge: #8a8a8a;
  }
  * { box-sizing: border-box; margin: 0; padding: 0; }
  html, body {
    width: 1200px;
    height: 995px;
    overflow: hidden;
    background: var(--backdrop);
    font-family: "Source Sans 3", "Myriad Pro", sans-serif;
  }
  .canvas {
    position: relative;
    width: 1200px;
    height: 995px;
  }
  .card {
    position: absolute;
    background: var(--card-white);
    border: 1px solid var(--card-edge);
    overflow: hidden;
    box-shadow: 0 2px 6px rgba(0,0,0,0.12);
  }

  /* Front */
  .card--front { left: 54px; top: 45px; width: 756px; height: 432px; }
  .brand-name {
    position: absolute;
    left: 0; right: 0; top: 118px;
    text-align: center;
    color: var(--brand-blue);
    font-weight: 700;
    font-size: 44px;
    line-height: 1.1;
    text-transform: uppercase;
    letter-spacing: 0.5px;
  }
  .front-band {
    position: absolute;
    left: 0; top: 0;
    width: 756px; height: 432px;
  }
  .contact-list {
    position: absolute;
    left: 0; right: 0; top: 320px;
    list-style: none;
    text-align: center;
    color: var(--card-white);
    font-size: 21px;
    line-height: 32.5px;
  }
  .contact-list li { display: flex; justify-content: center; align-items: center; gap: 7px; }
  .contact-icon { width: 16px; height: 16px; fill: var(--card-white); }

  /* Back */
  .card--back { left: 387px; top: 515px; width: 755px; height: 430px; }
  .services-panel {
    position: absolute;
    left: 31px; top: 178px;
    width: 690px; height: 157px;
    background: var(--brand-blue);
    border-radius: 18px;
    color: var(--card-white);
    text-align: center;
  }
  .services-title {
    margin-top: 20px;
    font-size: 29px;
    font-weight: 600;
    letter-spacing: 2.5px;
  }
  .services-list {
    list-style: none;
    margin-top: 14px;
    font-size: 23px;
    font-weight: 600;
    line-height: 34px;
    text-transform: uppercase;
  }
  .back-web {
    position: absolute;
    left: 0; right: 0; top: 372px;
    text-align: center;
    color: var(--ink);
    font-size: 27px;
    letter-spacing: 2.5px;
  }
</style>
</head>
<body>
<main class="canvas">

  <section class="card card--front" aria-label="Card front">
    <h1 class="brand-name">Brightway Haul<br>&amp; Upkeep Services</h1>

    <svg class="front-band" viewBox="0 0 756 432" aria-hidden="true">
      <path d="M0 362 Q378 218 756 362 L756 432 L0 432 Z" fill="var(--brand-blue)"/>
      <path d="M0 358 Q378 210 756 358" fill="none" stroke="var(--ink)" stroke-width="4"/>
    </svg>

    <ul class="contact-list">
      <li>
        <svg class="contact-icon" viewBox="0 0 16 16" aria-hidden="true"><path d="M3.5 1.5l2.5 2.8-1.4 1.8c.9 2 2.4 3.5 4.3 4.4l1.8-1.4 2.8 2.5-1.6 2.3C6.8 13.4 2.6 9.2 1.2 3.1z"/></svg>
        0487650392
      </li>
      <li>
        <svg class="contact-icon" viewBox="0 0 16 16" aria-hidden="true"><path d="M8 1a7 7 0 100 14A7 7 0 008 1zm0 1.5c.6 0 1.5 1.4 1.9 3.5H6.1C6.5 3.9 7.4 2.5 8 2.5zM2.6 7.2h2.3a12 12 0 000 1.6H2.6a5.5 5.5 0 010-1.6zm3.5 2.8h3.8C9.5 12.1 8.6 13.5 8 13.5S6.5 12.1 6.1 10zm0-2.8h3.8a10 10 0 010 1.6H6.1a10 10 0 010-1.6zm5 0h2.3a5.5 5.5 0 010 1.6h-2.3a12 12 0 000-1.6z"/></svg>
        www.brightwayhaul.com.au
      </li>
      <li>
        <svg class="contact-icon" viewBox="0 0 16 16" aria-hidden="true"><path d="M1 6l7-4 7 4v8H1zm1.5 1v.4L8 10.6l5.5-3.2V7L8 3.8z"/></svg>
        brightwayhaulandupkeep@mailbox.example
      </li>
    </ul>
  </section>

  <section class="card card--back" aria-label="Card back">
    <div class="services-panel">
      <h2 class="services-title">Services we offer</h2>
      <ul class="services-list">
        <li>• Clean • Move</li>
        <li>• General maintenance and repairs.</li>
      </ul>
    </div>
    <p class="back-web">www.brightwayhaul.com.au</p>
  </section>

</main>
</body>
</html>
```